I have a website called Okenta Holdings (okentaholdings.com) that I would like to have redesigned. Most of the content is already created, but I need a new design. You can also see my other website at brambleacres.com. I am open to a new logo or modifying the current logo if you have a good idea. Please feel free to use other images for the home page (and maybe some other locations) if you feel they provide a better look and feel to the website. I prefer a modern look.

Important: You do not have to use the images I've provided for the home page. Feel free to find your own stock photos. You don't have to pay for them unless I select your design.

1) Please use wix.com to make your changes so that I can edit it later.
2) I will need all the graphics files to be saved so I can dowload it for later.
3) I will be adding more content to the site later.
4) This site will likely be transferred over to brambleacres.com so if you make a logo please make one for Okenta Holdings and one for Bramble Acres.
5) You can use other images that you feel would help the look and feel of the website.

```html
<!DOCTYPE html>
<html lang="en">
<head>
<meta charset="utf-8">
<title>Bramble Acres</title>
<link href="https://fonts.googleapis.com/css2?family=Montserrat:wght@500;600;700&family=Roboto:wght@400;500&display=swap" rel="stylesheet">
<style>
:root{
  --navy:#0d2b52;
  --navy-deep:#0a2344;
  --footer:#0a4178;
  --footer-bar:#08335f;
  --accent:#f0803c;
  --ink:#1d1d1d;
  --muted:#555;
  --line:#c9c9c9;
  --band:#f5f5f5;
  --white:#fff;
}
*{box-sizing:border-box;margin:0;padding:0}
html,body{width:1200px;height:4535px;overflow:hidden;background:var(--white)}
body{font-family:"Roboto",sans-serif;color:var(--ink);position:relative}
.abs{position:absolute}
h1,h2,h3,.heading{font-family:"Montserrat",sans-serif}
/* top bar */
.topbar{top:0;left:0;width:1200px;height:48px;border-bottom:1px solid #e3e3e3}
.social{display:flex;gap:14px}
.social span{width:24px;height:24px;border-radius:50%;background:var(--navy);display:block}
.topbar .social{position:absolute;left:63px;top:12px}
.top-contact{position:absolute;right:63px;top:14px;display:flex;gap:32px;font-size:15px;color:var(--navy)}
.top-contact span{display:flex;align-items:center;gap:10px}
/* nav */
.nav{top:48px;left:0;width:1200px;height:95px}
.brand{position:absolute;left:63px;top:30px;display:flex;align-items:center;gap:10px;font-family:"Montserrat",sans-serif;font-weight:700;font-size:20px;color:var(--navy)}
.brand i{width:28px;height:28px;background:var(--navy);display:block}
.menu{position:absolute;left:432px;top:38px;display:flex;gap:33px;font-family:"Montserrat",sans-serif;font-weight:600;font-size:15px;color:var(--navy)}
.nav-btn{position:absolute;left:977px;top:19px;width:160px;height:57px;background:var(--navy-deep);color:#fff;font:600 15px "Montserrat",sans-serif;display:flex;align-items:center;justify-content:center}
/* hero */
.hero{top:143px;left:0;width:1200px;height:635px;background:linear-gradient(180deg,#6f7ea6 0%,#4d5f86 45%,#3c4560 80%,#3a3f48 100%)}
.hero h1{position:absolute;top:150px;width:100%;text-align:center;color:#fff;font-weight:700;font-size:37px;line-height:57px}
.hero p{position:absolute;top:278px;width:100%;text-align:center;color:#fff;font-size:24px}
.hero .ghost{position:absolute;left:487px;top:362px;width:222px;height:56px;border:2px solid #fff;color:#fff;font:600 15px "Montserrat",sans-serif;display:flex;align-items:center;justify-content:center}
.chat{position:absolute;left:1072px;top:511px;width:64px;height:64px;border-radius:50%;background:#fff}
/* about */
.photo{background:linear-gradient(160deg,#9fc0e0,#d9d6cf 55%,#8b7a63)}
.about-img{top:885px;left:63px;width:373px;height:386px;box-shadow:0 6px 14px rgba(0,0,0,.2)}
.about{top:890px;left:516px;width:621px}
.about h2{font-size:38px;color:var(--navy);font-weight:600}
.rule{width:112px;height:3px;background:var(--navy);margin-top:22px}
.about p{margin-top:32px;font-size:17px;line-height:28px;color:#333}
.stats{display:flex;margin-top:30px}
.stat{width:198px;text-align:center;border-right:2px solid var(--accent);padding:6px 0 4px}
.stat:last-child{border:none}
.stat b{display:block;font:600 30px "Montserrat",sans-serif;color:var(--accent)}
.stat span{display:block;margin-top:18px;font:600 17px/28px "Montserrat",sans-serif;color:var(--navy)}
/* projects */
.section-title{width:1200px;left:0;text-align:center;font-size:37px;font-weight:600;color:var(--navy)}
.section-rule{left:551px;width:98px;height:3px;background:var(--navy)}
.project{width:347px}
.project .photo{height:245px}
.project h3{margin-top:28px;font-size:18px;font-weight:700;color:var(--navy)}
.project p{margin-top:18px;font-size:17px;line-height:29px;color:#222}
.show-line{top:2457px;left:63px;width:1074px;height:2px;background:var(--navy)}
.show-btn{top:2430px;left:487px;width:222px;height:56px;background:#fff;border:2px solid var(--navy);color:var(--navy);font:600 15px "Montserrat",sans-serif;display:flex;align-items:center;justify-content:center}
/* contact */
.contact{top:2583px;left:0;width:1200px;height:678px;background:linear-gradient(135deg,#2a4670,#1e3a62 50%,#2d4b73)}
.contact h2{position:absolute;left:63px;top:88px;color:#fff;font-size:37px;font-weight:600}
.contact .rule{position:absolute;left:63px;top:150px;background:#fff;margin:0}
.contact .lead{position:absolute;left:63px;top:180px;width:310px;color:#fff;font-size:17px;line-height:28px}
.info{display:flex;gap:22px;color:#fff;font-size:17px;line-height:28px}
.info svg{flex:none;margin-top:4px}
.form{position:absolute;left:433px;top:72px;width:704px;height:530px;background:#fff}
.field{position:absolute;border:1px solid #bdbdbd;color:#8a8a8a;font-size:17px;padding:11px 17px}
.submit{position:absolute;left:30px;top:437px;width:222px;height:57px;background:var(--navy-deep);color:#fff;font:600 15px "Montserrat",sans-serif;display:flex;align-items:center;justify-content:center}
/* map */
.map{top:3352px;left:63px;width:1074px;height:533px;background:linear-gradient(135deg,#e9e6e0,#dcdad4 50%,#e8e3da)}
.hq{top:3373px;left:746px;width:370px;height:308px;background:#fff;box-shadow:0 2px 10px rgba(0,0,0,.15);padding:30px 28px}
.hq h2{font-size:37px;font-weight:600;color:var(--navy)}
.hq .rule{width:110px}
.hq .info{color:#222;margin-top:24px;font-size:17px}
.zoom{top:3760px;left:1060px;width:56px;height:108px;background:#fff;box-shadow:0 1px 4px rgba(0,0,0,.3);font:400 40px/54px "Roboto",sans-serif;text-align:center;color:#333}
/* partners */
.partners{top:3971px;left:0;width:1200px;height:134px;background:var(--band);display:flex;justify-content:center;align-items:center;gap:72px;font:700 28px "Montserrat",sans-serif;color:#555}
/* footer */
.footer{top:4105px;left:0;width:1200px;height:347px;background:var(--footer);color:#fff}
.footer h3{font-size:24px;font-weight:600}
.col{position:absolute;top:62px}
.col ul{list-style:none;margin-top:36px;font-size:17px}
.col li{margin-bottom:20px}
.footer .info{margin-top:22px;font-size:17px}
.news-input{position:absolute;top:0;left:0;width:344px;height:56px;background:#fff;color:#888;font-size:17px;padding:17px 16px}
.news-btn{position:absolute;top:0;left:362px;width:166px;height:56px;background:#fff;color:var(--navy);font:700 15px "Montserrat",sans-serif;display:flex;align-items:center;justify-content:center}
.bottom{top:4452px;left:0;width:1200px;height:83px;background:var(--footer-bar);color:#fff;font-size:15px}
.bottom p{position:absolute;left:63px;top:32px}
.bottom .social{position:absolute;right:63px;top:30px}
.bottom .social span{background:#fff}
</style>
</head>
<body>

<header class="abs topbar">
  <div class="social" aria-label="Social links"><span></span><span></span><span></span></div>
  <div class="top-contact">
    <span><svg width="16" height="16" viewBox="0 0 24 24"><path d="M6.6 10.8a15 15 0 0 0 6.6 6.6l2.2-2.2a1 1 0 0 1 1-.25 11 11 0 0 0 3.6.6 1 1 0 0 1 1 1V20a1 1 0 0 1-1 1A17 17 0 0 1 3 4a1 1 0 0 1 1-1h3.5a1 1 0 0 1 1 1 11 11 0 0 0 .6 3.6 1 1 0 0 1-.25 1z" fill="#0d2b52"/></svg>(555) 014-2290</span>
    <span><svg width="22" height="16" viewBox="0 0 22 16"><rect width="22" height="16" rx="1" fill="#0d2b52"/><path d="M1 1l10 8 10-8" stroke="#fff" stroke-width="2" fill="none"/></svg>info@brambleacres.com</span>
  </div>
</header>

<nav class="abs nav">
  <div class="brand"><i></i>Bramble Acres</div>
  <div class="menu"><span>HOME</span><span>ABOUT</span><span>STRATEGY</span><span>PROJECT</span><span>CONTACT</span></div>
  <div class="nav-btn">CONTACT US</div>
</nav>

<section class="abs hero" role="img" aria-label="High-rise glass apartment tower against a blue dusk sky">
  <h1>PRIVATE COMMERCIAL REAL ESTATE<br>INVESTMENT AND DEVELOPMENT FIRM</h1>
  <p>Building together. Growing Together.</p>
  <div class="ghost">CONTACT US</div>
  <svg class="abs" style="left:588px;top:525px" width="24" height="110" viewBox="0 0 24 110"><line x1="12" y1="0" x2="12" y2="30" stroke="#fff" stroke-width="2" stroke-dasharray="4 4"/><rect x="4" y="34" width="16" height="26" rx="8" stroke="#fff" stroke-width="2" fill="none"/><line x1="12" y1="40" x2="12" y2="46" stroke="#fff" stroke-width="2"/><line x1="12" y1="64" x2="12" y2="108" stroke="#fff" stroke-width="2" stroke-dasharray="4 4"/></svg>
  <div class="chat"><svg width="64" height="64" viewBox="0 0 64 64"><ellipse cx="32" cy="31" rx="13" ry="10" fill="none" stroke="#333" stroke-width="2"/><circle cx="27" cy="31" r="1.6" fill="#333"/><circle cx="32" cy="31" r="1.6" fill="#333"/><circle cx="37" cy="31" r="1.6" fill="#333"/></svg></div>
</section>

<div class="abs photo about-img" role="img" aria-label="White residential tower above a terracotta-roofed low-rise building"></div>
<section class="abs about">
  <h2>About Us</h2>
  <div class="rule"></div>
  <p>Bramble Acres is a private real estate firm that specializes in the procurement, development, management, and disposition of various commercial real estate asset types including multifamily, industrial, single-family, hospitality, self-storage, and flex.</p>
  <div class="stats">
    <div class="stat"><b>2017</b><span>Year Established</span></div>
    <div class="stat"><b>Dallas, TX</b><span>Hear Quarters</span></div>
    <div class="stat"><b>$100MM+</b><span>Assets Under<br>Management</span></div>
  </div>
</section>

<h2 class="abs section-title" style="top:1390px">Discover Our Featured Projects</h2>
<div class="abs section-rule" style="top:1458px"></div>

<article class="abs project" style="left:63px;top:1513px"><div class="photo" role="img" aria-label="Mid-rise residential building with landscaped street"></div><h3>Lakeview Crest Residences</h3><p>Class A Multifamily - 176 Units - 4 Story - 159,280 SF - 3 Acres<br>Ground-up Development</p></article>
<article class="abs project" style="left:426px;top:1513px"><div class="photo" role="img" aria-label="Rendering of apartment blocks around a green courtyard"></div><h3>Willowmere in Cedar Hollow</h3><p>Class A Multifamily - 373 Units - 3 Story - 345,297 SF - 24.31 Acres<br>Ground-up Development</p></article>
<article class="abs project" style="left:790px;top:1513px"><div class="photo" role="img" aria-label="White industrial warehouse under a clear blue sky" style="background:linear-gradient(180deg,#2f6fd0,#8fb4e6 55%,#cfcfcf)"></div><h3>Trinity Logistics Park</h3><p>Class A Industrial - 170,000 SF - 10.10 Acres<br>Ground-up Development</p></article>

<article class="abs project" style="left:63px;top:1964px"><div class="photo" role="img" aria-label="Modern three-story townhomes with red doors" style="background:linear-gradient(160deg,#a9c8e6,#d8d2c8 55%,#7e7f7a)"></div><h3>Halden Homes</h3><p>Class A Multifamily - 23 Units - 3 Story - 42,000 SF - .78 Acres<br>Ground-up Development</p></article>
<article class="abs project" style="left:426px;top:1964px"><div class="photo" role="img" aria-label="Apartment complex entry sign with flowering landscaping" style="background:linear-gradient(180deg,#5b8fc9,#7e9a7a 55%,#6d5a7c)"></div><h3>Pine Ridge Apartments</h3><p>Class C Multifamily - 212 Units - 2 Story - 136,936 SF - 11.24 Acres<br>Value-Add Acquisition</p></article>
<article class="abs project" style="left:790px;top:1964px"><div class="photo" role="img" aria-label="Colorful red and tan apartment buildings with trees" style="background:linear-gradient(180deg,#6f9fd6,#a05a4f 50%,#5f7a4c)"></div><h3>Canvas at Midtown</h3><p>Class A Multifamily - 244 Units - 4 Story - 230,428 SF - 4.89 Acres<br>Value-Add Acquisition</p></article>

<div class="abs show-line"></div>
<div class="abs show-btn">SHOW ALL</div>

<section class="abs contact" role="img" aria-label="Dimmed kitchen interior behind a navy overlay">
  <h2>Contact Us</h2>
  <div class="rule"></div>
  <p class="lead">For any inquiries, questions or commendations, please fill in the following form.</p>
  <div class="abs info" style="left:63px;top:282px;width:330px"><svg width="20" height="18" viewBox="0 0 20 18"><path d="M1 3l6-2 6 2 6-2v14l-6 2-6-2-6 2z" fill="none" stroke="#fff" stroke-width="1.8"/><path d="M7 1v14M13 3v14" stroke="#fff" stroke-width="1.8"/></svg><span>1480 Alder Ave. 7th Floor<br>Dallas, Texas 75201</span></div>
  <div class="abs info" style="left:63px;top:349px;font-size:15px"><svg width="20" height="18" viewBox="0 0 24 24"><path d="M6.6 10.8a15 15 0 0 0 6.6 6.6l2.2-2.2a1 1 0 0 1 1-.25 11 11 0 0 0 3.6.6 1 1 0 0 1 1 1V20a1 1 0 0 1-1 1A17 17 0 0 1 3 4a1 1 0 0 1 1-1h3.5a1 1 0 0 1 1 1 11 11 0 0 0 .6 3.6 1 1 0 0 1-.25 1z" fill="#fff"/></svg><span>(555) 014-2290</span></div>
  <div class="abs info" style="left:63px;top:391px;font-size:15px"><svg width="22" height="16" viewBox="0 0 22 16"><rect width="22" height="16" rx="1" fill="#fff"/><path d="M1 1l10 8 10-8" stroke="#1e3a62" stroke-width="2" fill="none"/></svg><span>info@brambleacres.com</span></div>
  <div class="form">
    <div class="field" style="left:30px;top:36px;width:315px;height:46px">First Name</div>
    <div class="field" style="left:358px;top:36px;width:315px;height:46px">Last Name</div>
    <div class="field" style="left:30px;top:100px;width:644px;height:46px">Email</div>
    <div class="field" style="left:30px;top:163px;width:644px;height:46px">Phone</div>
    <div class="field" style="left:30px;top:226px;width:644px;height:196px">Message</div>
    <div class="submit">SUBMIT</div>
  </div>
</section>

<div class="abs map" role="img" aria-label="Street map of downtown Dallas with a location pin"></div>
<div class="abs hq">
  <h2>Head Quarters</h2>
  <div class="rule"></div>
  <div class="info"><svg width="20" height="18" viewBox="0 0 20 18"><path d="M1 3l6-2 6 2 6-2v14l-6 2-6-2-6 2z" fill="none" stroke="#222" stroke-width="1.8"/><path d="M7 1v14M13 3v14" stroke="#222" stroke-width="1.8"/></svg><span>1480 Alder Ave. 7th Floor<br>Dallas, Texas 75201</span></div>
  <div class="info" style="font-size:15px"><svg width="20" height="18" viewBox="0 0 24 24"><path d="M6.6 10.8a15 15 0 0 0 6.6 6.6l2.2-2.2a1 1 0 0 1 1-.25 11 11 0 0 0 3.6.6 1 1 0 0 1 1 1V20a1 1 0 0 1-1 1A17 17 0 0 1 3 4a1 1 0 0 1 1-1h3.5a1 1 0 0 1 1 1 11 11 0 0 0 .6 3.6 1 1 0 0 1-.25 1z" fill="#222"/></svg><span>(555) 014-2290</span></div>
  <div class="info" style="font-size:15px;margin-top:18px"><svg width="22" height="16" viewBox="0 0 22 16"><rect width="22" height="16" rx="1" fill="#222"/><path d="M1 1l10 8 10-8" stroke="#fff" stroke-width="2" fill="none"/></svg><span>info@brambleacres.com</span></div>
</div>
<div class="abs zoom">+<br>−</div>

<div class="abs partners"><span>NORVA</span><span>LUMETRA</span><span>Quill</span><span>STAYWELL</span><span>ASHFORD &amp; CO</span></div>

<footer class="abs footer">
  <div class="col" style="left:63px"><h3>Discover</h3><ul><li>- About Us</li><li>- Strategy</li><li>- Project</li><li>- Job Offer</li></ul></div>
  <div class="col" style="left:245px"><h3>Contact</h3>
    <div class="info" style="margin-top:36px"><svg width="20" height="18" viewBox="0 0 20 18"><path d="M1 3l6-2 6 2 6-2v14l-6 2-6-2-6 2z" fill="none" stroke="#fff" stroke-width="1.8"/><path d="M7 1v14M13 3v14" stroke="#fff" stroke-width="1.8"/></svg><span>1480 Alder Ave. 7th Floor<br>Dallas, Texas 75201</span></div>
    <div class="info" style="font-size:15px"><svg width="20" height="18" viewBox="0 0 24 24"><path d="M6.6 10.8a15 15 0 0 0 6.6 6.6l2.2-2.2a1 1 0 0 1 1-.25 11 11 0 0 0 3.6.6 1 1 0 0 1 1 1V20a1 1 0 0 1-1 1A17 17 0 0 1 3 4a1 1 0 0 1 1-1h3.5a1 1 0 0 1 1 1 11 11 0 0 0 .6 3.6 1 1 0 0 1-.25 1z" fill="#fff"/></svg><span>(555) 014-2290</span></div>
    <div class="info" style="font-size:15px;margin-top:14px"><svg width="22" height="16" viewBox="0 0 22 16"><rect width="22" height="16" rx="1" fill="#fff"/><path d="M1 1l10 8 10-8" stroke="#0a4178" stroke-width="2" fill="none"/></svg><span>info@brambleacres.com</span></div>
  </div>
  <div class="col" style="left:608px;width:530px"><h3>Newsletter</h3>
    <p style="margin-top:36px;font-size:17px">Subscribe to our newsletter right now to be updated.</p>
    <div style="position:relative;margin-top:24px;height:56px"><div class="news-input">Your Email</div><div class="news-btn">SUBSCRIBE</div></div>
  </div>
</footer>
<div class="abs bottom"><p>Copyrights © 2023, Keystone Buildworks. All rights reserved.</p><div class="social" aria-label="Social links"><span></span><span></span><span></span></div></div>

</body>
</html>
```